Blue Fern Handcrafted Tomato Ketchup packaging design modern

From the best ingredients there is the best ketchup Blue Handcrafted ketchup are specially formulated for fine dining and drinks, bringing out all the flavors. As the Blue Fern handcrafted ketchup is otherwise fabulous: Made with wholesome, fully ripe fruits Nothing with half things! All Blue Fern handcrafted ketchups are pure nature, without any artificial diluents or concentrates. Where tomato is on it, that's all there is to it - guaranteed! the design should be professional and noble despite being trendy. A watcher wants to sell the ketchup as merchandising from our restaurant. but as a single brand positioning. The ketchup is vegan. Dimensions: 6.8 cm Height: 7.8 cm Circumference: 21.6 cm The text down (Text 1-4). The lid of the text the glass packaging is black! Thanks for your efforts. I look forward to your designs.

Target Market(s)

foodies

Font styles to use
Serif
Sans Serif

Colors

Designer to choose colors to be used in the design.

Requirements
Must have
• Title: (Handcrafted Tomato Ketchup) Text One: (Store chilled after opening and consume quickly, pasteurized.) Text Two: (Handcrafted in Switzerland by Varentoli Kulina GmbH, Chur www.bluefern-vorel.example) Text Tree: (Tomatoes, White Wine Vinegar, Aceto Balsamico, Brown Cane Sugar, Corn Starch, Spices, Salt) Text For: (200 grams) or (200g) The Logo of Blue Fern with the Pasta and Wine have to because of the gesety.
Nice to have
• small vegan icon (maybe)
Should not have
• text of the logo (pasta & wine)

```html
<!DOCTYPE html>
<html lang="en">
<head>
<meta charset="utf-8">
<title>Blue Fern Handcrafted Tomato Ketchup – Jar Label</title>
<link href="https://fonts.googleapis.com/css2?family=Bebas+Neue&family=Josefin+Sans:wght@300;400&display=swap" rel="stylesheet">
<style>
  :root {
    --backdrop: #eceef2;
    --label-light: #e4e4e6;
    --label-mid: #bdbdbf;
    --label-edge: #f2f2f3;
    --ink: #1c1c1c;
    --band: #151515;
    --band-text: #ffffff;
  }
  * { margin: 0; padding: 0; box-sizing: border-box; }
  html, body { width: 1200px; height: 1200px; overflow: hidden; }
  body {
    background: var(--backdrop);
    position: relative;
    font-family: "Josefin Sans", sans-serif;
    color: var(--ink);
  }
  .label {
    position: absolute;
    left: 127px; top: 57px;
    width: 946px; height: 1086px;
    background: linear-gradient(90deg,
      var(--label-edge) 0%, var(--label-edge) 13%,
      var(--label-mid) 16%, var(--label-light) 45%,
      var(--label-mid) 80%, var(--label-edge) 86%, var(--label-edge) 100%);
    box-shadow: 0 10px 30px rgba(0,0,0,.12);
  }
  .brand-frame {
    position: absolute;
    left: 216px; top: 66px;
    width: 525px; height: 571px;
    border: 6px solid var(--ink);
    text-align: center;
  }
  .brand-name {
    margin-top: 38px;
    font-family: "Josefin Sans", sans-serif;
    font-weight: 400;
    font-size: 88px;
    line-height: 1;
    letter-spacing: 1px;
  }
  .brand-rule {
    width: 440px; height: 5px;
    margin: 22px auto 0;
    background: var(--ink);
  }
  .product-title {
    font-family: "Bebas Neue", sans-serif;
    transform: skewX(-10deg);
    line-height: .95;
  }
  .product-title span { display: block; }
  .title-handcrafted { font-size: 92px; margin-top: 24px; letter-spacing: 2px; }
  .title-tomato { font-size: 178px; letter-spacing: 2px; }
  .title-ketchup { font-size: 108px; letter-spacing: 26px; margin-left: 26px; }
  .storage-note {
    position: absolute;
    left: 0; top: 670px; width: 100%;
    text-align: center;
    font-size: 31px; line-height: 41px;
    font-weight: 400;
  }
  .maker {
    position: absolute;
    left: 0; top: 790px; width: 100%;
    text-align: center;
    font-size: 21px; line-height: 30px;
    font-weight: 400;
  }
  .ingredients {
    position: absolute;
    left: 14px; right: 14px; top: 886px;
    height: 44px;
    background: var(--band);
    color: var(--band-text);
    font-size: 21px;
    line-height: 46px;
    text-align: center;
    white-space: nowrap;
  }
  .net-weight {
    position: absolute;
    left: 0; top: 978px; width: 100%;
    text-align: center;
    font-size: 20px;
  }
</style>
</head>
<body>
  <main class="label">
    <section class="brand-frame">
      <h1 class="brand-name">BLUE FERN</h1>
      <div class="brand-rule"></div>
      <h2 class="product-title">
        <span class="title-handcrafted">HANDCRAFTED</span>
        <span class="title-tomato">TOMATO</span>
        <span class="title-ketchup">KETCHUP</span>
      </h2>
    </section>
    <p class="storage-note">Store chilled after opening and<br>consume quickly, pasteurized.</p>
    <p class="maker">Handcrafted in Switzerland by Varentoli Kulina GmbH, Chur<br>www.bluefern-vorel.example</p>
    <p class="ingredients">Tomatoes, White Wine Vinegar, Aceto Balsamico, Brown Cane Sugar, Corn Starch, Spices, Salt</p>
    <p class="net-weight">200 grams</p>
  </main>
</body>
</html>
```